The Plate Compass

Cutting Through the Noise to What Actually Works.

Nutrition book

Target Market(s)

People looking to be or get healthy and eat right.

```html
<!DOCTYPE html>
<html lang="en">
<head>
<meta charset="utf-8">
<title>The Plate Compass — Book Cover</title>
<link rel="stylesheet" href="https://fonts.googleapis.com/css2?family=Archivo+Black&family=Montserrat:wght@400;500;600;700&display=swap">
<style>
  :root {
    --paper: #f7f6f2;
    --ink: #161616;
    --green: #3f7d2c;
    --green-deep: #2f6a25;
    --green-soft: #dfe8d6;
    --rule: #b9cfa9;
    --muted: #333333;
  }
  * { margin: 0; padding: 0; box-sizing: border-box; }
  html, body { width: 800px; height: 1200px; overflow: hidden; background: var(--paper); }
  .cover {
    position: relative; width: 800px; height: 1200px;
    background: linear-gradient(90deg, #ecebe6 0, var(--paper) 18px, var(--paper) 100%);
    font-family: "Montserrat", sans-serif; color: var(--ink);
  }
  .abs { position: absolute; }
  .top-tagline {
    top: 27px; left: 0; width: 800px; text-align: center;
    font-size: 12.5px; font-weight: 500; letter-spacing: 3.6px;
  }
  .top-rule { top: 54px; left: 70px; width: 664px; height: 1px; background: var(--rule); }
  .title { top: 68px; left: 0; width: 800px; text-align: center; font-family: "Archivo Black", sans-serif; line-height: 1; }
  .title-the { font-size: 52px; letter-spacing: 4px; color: var(--ink); }
  .title-main { font-size: 138px; letter-spacing: -2px; color: var(--green); margin-top: 14px; }
  .title-sub { font-size: 132px; letter-spacing: -2px; color: var(--ink); margin-top: 8px; }
  .food-pyramid { top: 400px; left: 66px; width: 668px; height: 552px; }
  .features { top: 440px; left: 56px; width: 106px; text-align: center; }
  .feature { height: 140px; display: flex; flex-direction: column; align-items: center; }
  .feature-icon {
    width: 62px; height: 62px; border-radius: 50%; background: var(--green-soft);
    display: flex; align-items: center; justify-content: center;
  }
  .feature-label { margin-top: 13px; font-size: 11.5px; font-weight: 500; letter-spacing: 1px; line-height: 1.45; }
  .feature-rule { width: 90px; height: 1px; background: var(--rule); margin: -12px auto 12px; }
  .badge {
    top: 437px; left: 586px; width: 182px; height: 182px; border-radius: 50%;
    background: var(--green-deep); color: #fff; display: flex; flex-direction: column;
    align-items: center; justify-content: center; text-align: center;
    font-size: 16.5px; font-weight: 500; letter-spacing: 2.6px; line-height: 1.65;
  }
  .badge-dash { width: 22px; height: 1.5px; background: #fff; margin-top: 8px; }
  .subtitle { top: 980px; left: 0; width: 800px; text-align: center; font-size: 31px; line-height: 1.38; }
  .subtitle-lead { font-weight: 400; color: var(--ink); }
  .subtitle-strong { font-weight: 700; color: var(--green); }
  .author-rule { top: 1117px; height: 1px; background: var(--rule); }
  .author { top: 1102px; left: 0; width: 800px; text-align: center; font-size: 23px; font-weight: 500; letter-spacing: 5px; }
  .author-tagline { top: 1138px; left: 0; width: 800px; text-align: center; font-size: 9.5px; font-weight: 500; letter-spacing: 2.4px; color: var(--muted); }
</style>
</head>
<body>
<main class="cover">
  <p class="abs top-tagline">REAL FOOD. REAL SCIENCE. A HEALTHIER YOU.</p>
  <div class="abs top-rule"></div>

  <h1 class="abs title">
    <div class="title-the">THE</div>
    <div class="title-main">PLATE</div>
    <div class="title-sub">COMPASS</div>
  </h1>

  <svg class="abs food-pyramid" viewBox="0 0 668 552" role="img" aria-label="Food pyramid built from whole foods: chocolate and nuts at the top, salmon, egg and lentils, then grains, sweet potato and oats, then vegetables and fruit, with avocado, olive oil, nuts and seeds at the base">
    <defs>
      <linearGradient id="pyramidTones" x1="0" y1="0" x2="0" y2="1">
        <stop offset="0" stop-color="#5a3a28"/>
        <stop offset="0.22" stop-color="#e07a4a"/>
        <stop offset="0.45" stop-color="#c89a62"/>
        <stop offset="0.72" stop-color="#3f7a2a"/>
        <stop offset="1" stop-color="#6f7c34"/>
      </linearGradient>
    </defs>
    <polygon points="334,2 560,360 640,470 650,552 20,552 28,470 108,360" fill="url(#pyramidTones)" opacity="0.92"/>
  </svg>

  <div class="abs features">
    <div class="feature">
      <div class="feature-icon">
        <svg width="30" height="30" viewBox="0 0 30 30" fill="none" stroke="#1d3d14" stroke-width="1.8" stroke-linecap="round" stroke-linejoin="round">
          <path d="M7 24C5 14 12 6 24 5c1 12-7 19-17 19z"/><path d="M7 24L18 12"/>
        </svg>
      </div>
      <p class="feature-label">EVIDENCE<br>BASED</p>
    </div>
    <div class="feature-rule"></div>
    <div class="feature">
      <div class="feature-icon">
        <svg width="34" height="30" viewBox="0 0 34 30" fill="none" stroke="#1d1d1d" stroke-width="1.8" stroke-linejoin="round">
          <rect x="5" y="8" width="5" height="14" rx="1"/><rect x="24" y="8" width="5" height="14" rx="1"/>
          <rect x="1.5" y="11" width="3.5" height="8" rx="1"/><rect x="29" y="11" width="3.5" height="8" rx="1"/>
          <path d="M10 15h14"/>
        </svg>
      </div>
      <p class="feature-label">SUSTAINABLE<br>HABITS</p>
    </div>
    <div class="feature-rule"></div>
    <div class="feature">
      <div class="feature-icon">
        <svg width="32" height="30" viewBox="0 0 32 30" fill="none" stroke="#1d1d1d" stroke-width="1.9" stroke-linejoin="round">
          <path d="M16 26L4.5 14.5a6.5 6.5 0 0 1 11.5-8 6.5 6.5 0 0 1 11.5 8z"/>
        </svg>
      </div>
      <p class="feature-label">A HEALTHIER<br>HAPPIER YOU</p>
    </div>
  </div>

  <div class="abs badge">
    <span>SIMPLE</span><span>PRINCIPLES</span><span>FOR REAL</span><span>LIFE</span>
    <div class="badge-dash"></div>
  </div>

  <p class="abs subtitle">
    <span class="subtitle-lead">Cutting Through the Noise</span><br>
    <span class="subtitle-strong">to What Actually Works.</span>
  </p>

  <div class="abs author-rule" style="left:70px;width:141px"></div>
  <div class="abs author-rule" style="left:590px;width:140px"></div>
  <p class="abs author">JORDAN HALE, RDN</p>
  <p class="abs author-tagline">BETTER FOOD. BRIGHTER DAYS.</p>
</main>
</body>
</html>
```